Marcus Delane 'keep it low' CD cover design

Design a CD cover and a logo (using my initials- MD)
Basically the two files attached are what I'm looking for (front and back)
I'd like my image to stand out with a white background.
The logo will be something I use on all my albums and website.
I like the white bold look.
Possible enhance image marginally I've lost a little weight since taking the picture.
The music I perform is Jazz Swing

Jazz Swing Audience

```html
<!DOCTYPE html>
<html lang="en">
<head>
<meta charset="utf-8">
<title>Marcus Delane – keep it low</title>
<link href="https://fonts.googleapis.com/css2?family=Crimson+Text:ital@1&family=Arimo:wght@400;700&display=swap" rel="stylesheet">
<style>
  :root {
    --sky-top: #f4f4f4;
    --sky-mid: #b9b9b9;
    --snow: #ececec;
    --panel: rgba(40, 40, 40, 0.62);
    --track-ink: #ffffff;
    --ink: #111111;
    --suit-light: #d8d8d8;
    --suit-dark: #161616;
  }
  html, body {
    margin: 0;
    padding: 0;
    overflow: hidden;
    background: #ffffff;
  }
  .cover {
    position: relative;
    width: 1200px;
    height: 1021px;
    overflow: hidden;
    background: linear-gradient(180deg, var(--sky-top) 0%, #dcdcdc 22%, var(--sky-mid) 48%, #cfcfcf 66%, var(--snow) 80%, #ffffff 100%);
  }
  .landscape {
    position: absolute;
    inset: 0;
    background: radial-gradient(ellipse at 60% 30%, rgba(120,120,120,0.35), transparent 55%),
                radial-gradient(ellipse at 20% 10%, rgba(90,90,90,0.25), transparent 45%);
  }
  .tracklist-panel {
    position: absolute;
    left: 0;
    top: 199px;
    width: 672px;
    height: 623px;
    background: var(--panel);
  }
  .tracklist {
    position: absolute;
    left: 62px;
    top: 254px;
    margin: 0;
    padding: 0;
    list-style: none;
    font-family: "Crimson Text", "Times New Roman", serif;
    font-style: italic;
    font-size: 56px;
    line-height: 78px;
    color: var(--track-ink);
  }
  .tracklist li {
    display: flex;
  }
  .tracklist .num {
    width: 60px;
    flex: none;
  }
  .artist-photo {
    position: absolute;
    left: 600px;
    top: 185px;
    width: 600px;
    height: 836px;
    background: linear-gradient(180deg, rgba(60,60,60,0.0) 0%, var(--suit-light) 12%, #8a8a8a 35%, var(--suit-dark) 48%, var(--suit-dark) 100%);
    border-radius: 280px 280px 0 0;
  }
  .brand {
    position: absolute;
    right: 55px;
    top: 48px;
    font-family: "Arimo", Arial, sans-serif;
    font-weight: 700;
    font-size: 52px;
    line-height: 1;
    color: var(--ink);
    letter-spacing: -1px;
  }
  .website {
    position: absolute;
    left: 150px;
    top: 890px;
    width: 285px;
    text-align: center;
    font-family: "Arimo", Arial, sans-serif;
    font-size: 24px;
    line-height: 31px;
    color: var(--ink);
  }
</style>
</head>
<body>
  <main class="cover">
    <div class="landscape" role="img" aria-label="Black and white snowy landscape under a cloudy sky"></div>
    <div class="tracklist-panel"></div>
    <ol class="tracklist">
      <li><span class="num">1.</span><span>Teddy Bear</span></li>
      <li><span class="num">2.</span><span>Fly me to the moon</span></li>
      <li><span class="num">3.</span><span>It’s now or never</span></li>
      <li><span class="num">4.</span><span>Can’t take my eyes<br>off you</span></li>
      <li><span class="num">5.</span><span>Love story</span></li>
    </ol>
    <div class="artist-photo" role="img" aria-label="Portrait of Marcus Delane smiling in a black suit, white shirt and black tie"></div>
    <div class="brand">MD</div>
    <p class="website" style="margin:0">find out more at:<br>www.marcusdelane.com</p>
  </main>
</body>
</html>
```